VOMRA Pty Ltd Business Card

Looking for a simple yet eye-catching double-sided business card design using my company logo on one side and contact details on the other.

Target Market(s)

Government

Industry/Entity Type

Communication Systems Engineering

Contact Information for Business Card

VOMRA Pty Ltd

Requirements
Nice to have
• Would be great to have a QR code so details can be scanned into contacts

```html
<!DOCTYPE html>
<html lang="en">
<head>
<meta charset="utf-8">
<title>VOMRA Pty Ltd Business Card</title>
<link rel="stylesheet" href="https://fonts.googleapis.com/css2?family=Arimo:wght@400;700&display=swap">
<style>
  :root {
    --stage: #2a2a2a;
    --card-dark: #2f3942;
    --card-dark-edge: #3a4550;
    --card-light: #f7f7f7;
    --ink: #2e2e2e;
    --ink-soft: #5a5a5a;
    --brand: #2c3238;
    --silver: #b9c0c6;
  }
  * { box-sizing: border-box; margin: 0; padding: 0; }
  html, body { width: 1200px; height: 689px; overflow: hidden; }
  body {
    background: var(--stage);
    font-family: "Arimo", Arial, sans-serif;
    position: relative;
  }
  .card {
    position: absolute;
    top: 196px;
    width: 520px;
    height: 297px;
    border-radius: 16px;
  }
  .card-back {
    left: 50px;
    background: linear-gradient(160deg, var(--card-dark-edge), var(--card-dark));
  }
  .card-front {
    left: 630px;
    background: var(--card-light);
  }

  /* Back side */
  .back-mark {
    position: absolute;
    left: 0; right: 0; top: 92px;
    display: flex;
    justify-content: center;
    align-items: center;
    gap: 14px;
  }
  .back-mark .dot {
    width: 22px; height: 22px;
    border: 2px solid var(--silver);
    border-radius: 50%;
  }
  .back-mark .name {
    color: var(--silver);
    font-weight: 700;
    font-size: 44px;
    letter-spacing: 4px;
  }
  .back-url {
    position: absolute;
    left: 0; right: 0; bottom: 54px;
    text-align: center;
    color: var(--silver);
    font-size: 14px;
    letter-spacing: 3px;
  }

  /* Front side */
  .front-brand {
    position: absolute;
    left: 40px; top: 52px;
    display: flex;
    align-items: center;
    gap: 12px;
  }
  .front-brand .dot {
    width: 20px; height: 20px;
    border: 2px solid var(--brand);
    border-radius: 50%;
  }
  .front-brand .name {
    color: var(--brand);
    font-weight: 700;
    font-size: 38px;
    letter-spacing: 3px;
  }
  .person {
    position: absolute;
    left: 40px; top: 124px;
  }
  .person .full-name {
    font-weight: 700;
    font-size: 20px;
    color: var(--ink);
  }
  .person .role {
    font-size: 11px;
    color: var(--ink-soft);
    margin-top: 3px;
  }
  .address {
    position: absolute;
    left: 40px; top: 178px;
    font-size: 13px;
    line-height: 17px;
    color: var(--ink);
  }
  .contacts {
    position: absolute;
    left: 40px; top: 222px;
    list-style: none;
    font-size: 13px;
    line-height: 17px;
    color: var(--ink);
  }
  .contacts li { display: flex; align-items: center; gap: 8px; }
  .contacts svg { width: 10px; height: 10px; fill: var(--ink); }
</style>
</head>
<body>
  <section class="card card-back" aria-label="Business card, logo side">
    <div class="back-mark">
      <span class="dot"></span>
      <span class="name">VOMRA</span>
    </div>
    <p class="back-url">www.vomrasys.org</p>
  </section>

  <section class="card card-front" aria-label="Business card, contact side">
    <div class="front-brand">
      <span class="dot"></span>
      <span class="name">VOMRA</span>
    </div>
    <div class="person">
      <p class="full-name">Daniel Morgan</p>
      <p class="role">Managing Director</p>
    </div>
    <p class="address">4120 Harbour Street<br>Hobart, Tasmania 7000</p>
    <ul class="contacts">
      <li>
        <svg viewBox="0 0 10 10" aria-hidden="true"><path d="M2 0.5 L3.6 2.6 L2.7 3.8 Q3.8 6 6.2 7.3 L7.4 6.4 L9.5 8 L8.3 9.6 Q3.5 9 0.4 1.7 Z"/></svg>
        <span>555-201-4487</span>
      </li>
      <li>
        <svg viewBox="0 0 10 10" aria-hidden="true"><path d="M0 2 H10 V8.5 H0 Z M0.6 2.4 L5 5.8 L9.4 2.4" stroke="#f7f7f7" stroke-width="0.8"/></svg>
        <span>info@vomrasys.org</span>
      </li>
      <li>
        <svg viewBox="0 0 10 10" aria-hidden="true"><circle cx="5" cy="5" r="4.6"/><path d="M1 5 H9 M5 0.6 Q2.4 5 5 9.4 M5 0.6 Q7.6 5 5 9.4" stroke="#f7f7f7" stroke-width="0.7" fill="none"/></svg>
        <span>www.vomrasys.org</span>
      </li>
    </ul>
  </section>
</body>
</html>
```